Hvac and insulation company needs good looking business card design

We are hvac and insulation company and looking for a new business cards that look to today standards designs

Target Market(s)

homeowners

Industry/Entity Type

Hvac

Contact Information for Business Card

Name: Walter Brinoku
Home comfort consultant
address: 4827 Dunmore St #215 Oakland, CA 94619
office: 888-316-2790
cell: 510-742-3185
Lic.# 584261
Email: walter@corvane-hvac.com
Web: corvane-hvac.com

Requirements
Must have
• clean and sleek look
Nice to have
• simple with a clean look
Should not have
• to busy business card

```html
<!DOCTYPE html>
<html lang="en">
<head>
<meta charset="utf-8">
<title>Corvane Home Solutions – Business Card</title>
<link rel="stylesheet" href="https://fonts.googleapis.com/css2?family=Work+Sans:wght@400;500;600&display=swap">
<style>
  :root {
    --backdrop: #161616;
    --card: #1d1d1d;
    --card-edge: #262626;
    --accent: #f5891f;
    --ink: #f2f2f2;
    --ink-soft: #d9d9d9;
  }
  * { margin: 0; padding: 0; box-sizing: border-box; }
  html, body {
    width: 1200px;
    height: 900px;
    overflow: hidden;
    background: var(--backdrop);
    font-family: "Work Sans", Arial, sans-serif;
  }
  .canvas {
    position: relative;
    width: 1200px;
    height: 900px;
  }
  .card {
    position: absolute;
    left: 250px;
    width: 700px;
    height: 400px;
    background: linear-gradient(135deg, #222 0%, var(--card) 55%, #191919 100%);
    border: 1px solid var(--card-edge);
  }
  .card--front { top: 35px; }
  .card--back { top: 465px; }

  .brand {
    display: flex;
    align-items: center;
    gap: 14px;
    color: var(--accent);
    font-weight: 600;
  }
  .brand__mark {
    background: var(--accent);
    flex: none;
  }
  .brand__text { display: flex; flex-direction: column; line-height: 1; }
  .brand__name { letter-spacing: 1px; }
  .brand__tagline { letter-spacing: 3px; }

  .card--front .brand {
    position: absolute;
    left: 50%;
    top: 130px;
    transform: translateX(-50%);
  }
  .card--front .brand__mark { width: 54px; height: 54px; }
  .card--front .brand__name { font-size: 70px; }
  .card--front .brand__tagline { font-size: 21px; margin-top: 6px; }

  .license {
    position: absolute;
    left: 0;
    right: 0;
    bottom: 48px;
    text-align: center;
    color: var(--ink);
    font-size: 18px;
    letter-spacing: 1px;
  }

  .card--back .brand {
    position: absolute;
    left: 48px;
    top: 145px;
  }
  .card--back .brand__mark { width: 38px; height: 38px; }
  .card--back .brand__name { font-size: 50px; }
  .card--back .brand__tagline { font-size: 15px; margin-top: 5px; }

  .divider {
    position: absolute;
    left: 372px;
    top: 70px;
    width: 3px;
    height: 260px;
    background: var(--accent);
  }

  .contact {
    position: absolute;
    left: 400px;
    top: 78px;
    color: var(--ink);
  }
  .contact__name {
    color: var(--accent);
    font-size: 25px;
    font-weight: 500;
    letter-spacing: 0.5px;
    text-transform: uppercase;
    line-height: 1.1;
  }
  .contact__role {
    font-size: 17px;
    letter-spacing: 0.5px;
    margin-bottom: 10px;
  }
  .contact__address {
    font-size: 17px;
    font-style: normal;
    line-height: 1.3;
    margin-bottom: 8px;
    letter-spacing: 0.5px;
  }
  .contact__list { list-style: none; }
  .contact__item {
    display: flex;
    align-items: center;
    gap: 10px;
    font-size: 17px;
    line-height: 1.4;
    letter-spacing: 0.5px;
  }
  .contact__icon {
    width: 12px;
    height: 12px;
    flex: none;
    fill: none;
    stroke: var(--accent);
    stroke-width: 1.6;
  }
  .web__domain { color: var(--accent); }
</style>
</head>
<body>
<main class="canvas">

  <section class="card card--front" aria-label="Card front">
    <div class="brand">
      <span class="brand__mark"></span>
      <div class="brand__text">
        <span class="brand__name">corvane</span>
        <span class="brand__tagline">home solutions</span>
      </div>
    </div>
    <p class="license">Lic.# 584261</p>
  </section>

  <section class="card card--back" aria-label="Card back">
    <div class="brand">
      <span class="brand__mark"></span>
      <div class="brand__text">
        <span class="brand__name">corvane</span>
        <span class="brand__tagline">home solutions</span>
      </div>
    </div>

    <span class="divider"></span>

    <div class="contact">
      <h1 class="contact__name">Walter Brinoku</h1>
      <p class="contact__role">Home comfort consultant</p>
      <address class="contact__address">4827 Dunmore St<br>#215 Oakland, CA 94619</address>
      <ul class="contact__list">
        <li class="contact__item">
          <svg class="contact__icon" viewBox="0 0 12 12" aria-hidden="true"><path d="M3 1 L5 3.5 L4 5 Q5.5 7.5 7 8 L8.5 7 L11 9 L9.5 11 Q4 10 1 2.5 Z"/></svg>
          888-316-2790
        </li>
        <li class="contact__item">
          <svg class="contact__icon" viewBox="0 0 12 12" aria-hidden="true"><rect x="3" y="1" width="6" height="10" rx="1"/><line x1="5" y1="9" x2="7" y2="9"/></svg>
          510-742-3185
        </li>
        <li class="contact__item">
          <svg class="contact__icon" viewBox="0 0 12 12" aria-hidden="true"><rect x="1" y="2.5" width="10" height="7"/><path d="M1 2.5 L6 6.5 L11 2.5"/></svg>
          walter@corvane-hvac.com
        </li>
        <li class="contact__item">
          <svg class="contact__icon" viewBox="0 0 12 12" aria-hidden="true"><circle cx="6" cy="6" r="5"/><ellipse cx="6" cy="6" rx="2.2" ry="5"/><line x1="1" y1="6" x2="11" y2="6"/></svg>
          <span>www.<span class="web__domain">corvane-hvac</span>.com</span>
        </li>
      </ul>
    </div>
  </section>

</main>
</body>
</html>
```